Website design for Puddle Jump Kidscare

I need a website designed for my daycare business, Puddle Jump Kidscare, now that I have a new logo. My former website was ok but simple and I did not have a logo yet. It also was created by me using a template and was entirely pink. I loved the bright, happy feel of it but worried it might not appeal as much to potential clients who have sons. Therefore, I need a site which will appeal to both genders while still keeping the cheerful color scheme of my new logo, which has pinks, blue, green and cream.
Updates

Reason: Hello! I am still trying to download my new logo and am sorry it is taking me so long. Hopefully I will it posted by the end of today (US Eastern Standard Time). Thank you all very much for your patience!

Hello! I have finally managed to upload my new logo for you to use in designing my website. I'm sorry it took so long and greatly appreciate your time and creative efforts! I look forward to seeing what is submitted based on my logo design and its style/colors.

Many thanks!

Reason: As I've been traveling and posted my logo file late, I am extending my deadline. I am now back and can focus on providing more and better feedback. I appreciate your patience and submissions very much!

Reason: I need more time to provide feedback and make decisions.

Industry/Entity Type

Daycare

Colors
0192cd
33a6d7
86cae7
cadf82
fbf289
add136
e34197

```html
<!DOCTYPE html>
<html lang="en">
<head>
<meta charset="utf-8">
<title>Puddle Jump Kidscare</title>
<link href="https://fonts.googleapis.com/css2?family=Bubblegum+Sans&family=Source+Sans+3:wght@400;600;700&display=swap" rel="stylesheet">
<style>
:root{
  --blue:#2a9fd6;
  --blue-soft:#86cae7;
  --green:#b9d65a;
  --green-dark:#a4c43f;
  --pink:#e34197;
  --pink-soft:#f09cc9;
  --text:#6d7a86;
  --muted:#8a949c;
  --cream:#f7f6f2;
  --white:#ffffff;
}
*{margin:0;padding:0;box-sizing:border-box}
html,body{width:1024px;height:1200px;overflow:hidden;background:var(--white)}
body{position:relative;font-family:"Source Sans 3",sans-serif;color:var(--text)}
.abs{position:absolute}
.display{font-family:"Bubblegum Sans",cursive}

/* hero (drawn first so everything else sits above it) */
.hero{left:0;top:99px;width:1024px;height:449px;background:linear-gradient(90deg,#ece6d9 0%,#f3efe6 45%,#f8f6f1 70%,#f1efea 100%)}
.hero-photo{left:40px;top:116px;width:520px;height:354px;border-radius:46% 46% 0 0;background:radial-gradient(ellipse at 52% 38%,#f0c29c 0%,#eda57a 22%,#c9d65f 48%,rgba(205,218,110,.55) 66%,rgba(236,230,217,0) 78%)}
.hero-table{left:0;top:418px;width:780px;height:60px;background:linear-gradient(90deg,#f2d64a 0%,#f7a24a 25%,#f7e05a 50%,#5cb8e4 68%,#f09cc9 85%,rgba(240,156,201,0) 100%);opacity:.75;border-radius:8px 8px 0 0}
.hero-title{left:570px;top:222px;font-size:34px;line-height:32px;font-weight:400}
.hero-title .l1{color:var(--blue)}
.hero-title .l2{color:var(--pink)}
.hero-sub{left:574px;top:300px;font-size:14px;line-height:20px;color:var(--muted)}

/* header */
.brand{left:136px;top:24px;font-weight:700;font-size:26px;color:var(--blue);letter-spacing:.2px}
.contact-strip{left:440px;top:24px;display:flex;height:26px;align-items:center}
.contact-item{display:flex;align-items:center;gap:7px;padding:0 13px;font-size:10.5px;color:var(--muted);border-left:1px solid #e6e6e6;height:26px}
.contact-item svg{flex:none}

/* nav */
.nav{left:134px;top:76px;width:753px;height:41px;background:var(--green);border:2px solid #cfe394;display:flex;align-items:center;padding-left:14px}
.nav a{color:var(--white);text-decoration:none;font-weight:600;font-size:13.3px;padding:0 17px;height:37px;line-height:37px}
.nav a.active{background:var(--blue);padding:0 22px;margin-right:3px}

/* feature boxes */
.feature{top:470px;width:240px;height:254px;border:1px solid rgba(255,255,255,.6);color:var(--white)}
.feature h2{position:absolute;left:0;right:0;top:10px;text-align:center;font-size:23px;font-weight:400;letter-spacing:.5px}
.feature .shot{position:absolute;left:15px;top:53px;width:208px;height:99px}
.feature p{position:absolute;left:15px;right:10px;top:166px;font-size:10px;font-weight:700;line-height:14.6px}
.f-learn{left:136px;background:var(--blue-soft)}
.f-create{left:392px;background:var(--green)}
.f-share{left:649px;background:var(--pink-soft)}

/* welcome */
.welcome-photo{left:138px;top:770px;width:111px;height:167px;background:linear-gradient(160deg,#7b6a52,#c99b85 50%,#e2cfbf)}
.welcome-title{left:264px;top:764px;font-size:19px;font-weight:400;color:var(--blue)}
.welcome-text{left:264px;top:801px;width:360px;font-size:9.7px;line-height:14.5px}
.welcome-text b{font-weight:700;color:#5d6a76}
.welcome-text p+p{margin-top:14px}
.read-more{font-size:8px;font-weight:700;color:var(--blue);text-decoration:underline;letter-spacing:.2px}
.welcome-more{left:264px;top:918px}

/* news */
.news-title{left:649px;top:763px;font-size:19px;font-weight:400;color:var(--blue)}
.news-item{left:649px;width:245px;height:70px}
.news-date{position:absolute;left:0;top:0;width:47px;height:47px;background:var(--pink-soft);color:var(--white);text-align:center}
.news-date .d{display:block;font-size:17px;line-height:20px;padding-top:6px}
.news-date .m{display:block;font-size:7px}
.news-text{position:absolute;left:64px;top:-6px;width:182px;font-size:12px;line-height:20px;color:var(--muted)}
.news-text .read-more{font-size:7.5px;text-decoration:none;margin-left:6px}
.news-text .read-more::before{content:"\25B8 "}

/* footer */
.footer{left:0;top:998px;width:1024px;height:168px;background:var(--cream);border-top:1px solid #ececec}
.footer-brand{left:137px;top:1062px;font-weight:700;font-size:16px;color:var(--blue)}
.fcol h3{font-size:10.5px;font-weight:600;color:var(--blue);margin-bottom:9px}
.fcol ul{list-style:none}
.fcol li{font-size:9.5px;line-height:19.4px;color:var(--muted);letter-spacing:.4px}
.fcol.links li::before{content:"\203A";color:#c9c9c9;margin-right:9px}
.fcol li.current{color:var(--green-dark)}
.col-nav{left:314px;top:1029px}
.col-links{left:440px;top:1029px}
.col-contact{left:568px;top:1029px}
.col-contact li{display:flex;align-items:flex-start;gap:9px;line-height:24px}
.col-contact li svg{margin-top:6px;flex:none}
.col-contact .indent{padding-left:19px;margin-top:-5px}
.col-visit{left:762px;top:1029px}
.map{left:761px;top:1052px;width:127px;height:82px;background:linear-gradient(135deg,#e8e6e0 0%,#dcdad3 55%,#b9c7d6 56%,#c9d2dc 70%,#e6e3da 71%)}

.bottom-bar{left:0;top:1166px;width:1024px;height:34px;background:var(--green);color:var(--white);font-size:9.8px}
.bottom-bar .copy{position:absolute;left:136px;top:11px}
.bottom-bar .legal{position:absolute;right:160px;top:11px}
.bottom-bar .legal span{margin:0 8px}
</style>
</head>
<body>

<section>
  <div class="abs hero" role="img" aria-label="Smiling toddler playing with colourful modelling clay at a table"></div>
  <div class="abs hero-photo" role="img" aria-label="Toddler seated in a green chair"></div>
  <div class="abs hero-table" role="img" aria-label="Colourful play dough tubs on a table"></div>
  <h1 class="abs hero-title display"><span class="l1">Welcome to</span><br><span class="l2">Puddle Jump Kidscare</span></h1>
  <p class="abs hero-sub">a playspace where children can play,<br>create, and imagine!</p>
</section>

<header>
  <div class="abs brand">Puddle Jump Kidscare</div>
  <div class="abs contact-strip">
    <div class="contact-item">
      <svg width="16" height="16" viewBox="0 0 16 16"><circle cx="8" cy="9" r="5.5" fill="none" stroke="#add136" stroke-width="1.6"/><path d="M8 6v3.2l2 1.2" stroke="#add136" stroke-width="1.4" fill="none"/><path d="M2.5 3.5l2-1.5M13.5 3.5l-2-1.5" stroke="#add136" stroke-width="1.4"/></svg>
      (Mon - Fri) 8:00AM to 6:00PM
    </div>
    <div class="contact-item">
      <svg width="20" height="14" viewBox="0 0 20 14"><rect x="6" y="2" width="13" height="10" fill="none" stroke="#add136" stroke-width="1.4"/><path d="M6 2l6.5 5.5L19 2" fill="none" stroke="#add136" stroke-width="1.4"/><path d="M0 4h4M1 7h3M2 10h2" stroke="#add136" stroke-width="1.2"/></svg>
      hello@puddlejumpkids.com
    </div>
    <div class="contact-item">
      <svg width="14" height="14" viewBox="0 0 14 14"><path d="M3 1l2.5 3-1.5 1.5c.8 1.8 2.2 3.2 4 4L9.5 8l3 2.5-1.5 2.5C6 12.5 1.5 8 1 3z" fill="#add136"/></svg>
      +(555) 014-2233
    </div>
  </div>
  <nav class="abs nav">
    <a class="active" href="#">Home</a>
    <a href="#">About</a>
    <a href="#">Services</a>
    <a href="#">Hours and Fees</a>
    <a href="#">Policies</a>
    <a href="#">Photos</a>
    <a href="#">Testimonials</a>
    <a href="#">Contact Us</a>
  </nav>
</header>

<section>
  <article class="abs feature f-learn">
    <h2 class="display">LEARNING</h2>
    <div class="shot" role="img" aria-label="Children playing together with building toys" style="background:linear-gradient(120deg,#d9633f,#e8c9a0 50%,#5aa5d8)"></div>
    <p>We develop age-appropriate activities that introduce and strengthen academic and social skills.</p>
  </article>
  <article class="abs feature f-create">
    <h2 class="display">CREATIVITY</h2>
    <div class="shot" role="img" aria-label="Child with painted hands showing artwork" style="background:linear-gradient(120deg,#3f5a2a,#d9a79a 45%,#6b3fa0 75%,#4a6a2e)"></div>
    <p>We offer children a wide range of creative opportunities including art projects, toddler yoga lessons, afternoon tea parties, dress up play, and a large selection of books and games.</p>
  </article>
  <article class="abs feature f-share">
    <h2 class="display">SHARING</h2>
    <div class="shot" role="img" aria-label="Child and adult sharing a pretend tea party" style="background:linear-gradient(120deg,#8a6a4e,#e7c8b4 45%,#f08aa8 60%,#b0503a)"></div>
    <p>We strive to include enrichment activities that extend your child's understanding of the world and their role in it.</p>
  </article>
</section>

<section>
  <div class="abs welcome-photo" role="img" aria-label="Caregiver smiling with a young child"></div>
  <h2 class="abs welcome-title display">Welcome to Puddle Jump Kidscare!</h2>
  <div class="abs welcome-text">
    <p>We are a <b>licensed Group Family Day Care</b>, located in Brookfield's beautiful Riverside district. We are located on a pretty, tree-lined block on Willow Lane, between Oak and Cedar Avenues. We are a few blocks from the green line tram and the Harbor Road bus route, and we offer flexible hourly childcare, making it as easy as possible for busy parents on the go to arrange their children's care.</p>
    <p>We invite you to learn more about us and hope you will visit us soon</p>
  </div>
  <a class="abs read-more welcome-more" href="#">READ MORE</a>

  <h2 class="abs news-title display">Latest News</h2>
  <div class="abs news-item" style="top:801px">
    <div class="news-date"><span class="d">05</span><span class="m">May 2014</span></div>
    <p class="news-text">We are thrilled to have found a new cheerful space with a private backyard... <a class="read-more" href="#">READ MORE</a></p>
  </div>
  <div class="abs news-item" style="top:874px">
    <div class="news-date"><span class="d">05</span><span class="m">May 2014</span></div>
    <p class="news-text">We are thrilled to have found a new cheerful space with a private backyard... <a class="read-more" href="#">READ MORE</a></p>
  </div>
</section>

<footer>
  <div class="abs footer"></div>
  <div class="abs footer-brand">Puddle Jump Kidscare</div>
  <div class="abs fcol links col-nav">
    <h3>Navigation</h3>
    <ul><li class="current">Home</li><li>About</li><li>Services</li><li>Contact</li></ul>
  </div>
  <div class="abs fcol links col-links">
    <h3>Links</h3>
    <ul><li>Menu1</li><li>Menu1</li><li>Menu1</li><li>Menu1</li></ul>
  </div>
  <div class="abs fcol col-contact">
    <h3>Contact Us</h3>
    <ul>
      <li><svg width="10" height="10" viewBox="0 0 14 14"><path d="M3 1l2.5 3-1.5 1.5c.8 1.8 2.2 3.2 4 4L9.5 8l3 2.5-1.5 2.5C6 12.5 1.5 8 1 3z" fill="#c4c4c4"/></svg>+1800-123-4567</li>
      <li><svg width="10" height="8" viewBox="0 0 12 9"><rect width="12" height="9" fill="#c4c4c4"/><path d="M0 0l6 5 6-5" fill="none" stroke="#f7f6f2" stroke-width="1"/></svg>info@yourwebsite.com</li>
      <li><svg width="10" height="12" viewBox="0 0 10 13"><path d="M5 0a4.5 4.5 0 0 1 4.5 4.5C9.5 8 5 13 5 13S.5 8 .5 4.5A4.5 4.5 0 0 1 5 0z" fill="#c4c4c4"/><circle cx="5" cy="4.5" r="1.6" fill="#f7f6f2"/></svg>Address, Your Country</li>
      <li class="indent">Your Zip Code</li>
    </ul>
  </div>
  <div class="abs fcol col-visit"><h3>Visit Us</h3></div>
  <div class="abs map" role="img" aria-label="Street map showing the daycare location"></div>

  <div class="abs bottom-bar">
    <span class="copy">Copyright 2014 © CompanyName - All Rights Reserved</span>
    <span class="legal">Site Map<span>•</span>Privacy Policy</span>
  </div>
</footer>

</body>
</html>
```